Home Security Company Business Card

Looking for a eye catching business card that is non traditional and stands out but yet still looks professional. It should include all the pertinent information such as name, title, address, telephone, e-mail, website address should definitely stand out and then finally the logo.

Target Market(s)

Residential and Commercial accounts mostly upscale accounts

Industry/Entity Type

Security

Contact Information for Business Card

Name
Title
Address
Office #
Cell #
E-mail
Website

Font styles to use
Serif
Sans Serif

Requirements
Must have
• Logo, two sided color configuration
Nice to have
• You decide
Should not have
• There really aren't any.

```html
<!DOCTYPE html>
<html lang="en">
<head>
<meta charset="utf-8">
<title>Ironvale Security Systems Inc. – Business Card</title>
<link href="https://fonts.googleapis.com/css2?family=Tinos:wght@400&family=Open+Sans:wght@400;600;700&display=swap" rel="stylesheet">
<style>
  :root {
    --backdrop: #9a9896;
    --card-black: #030303;
    --info-strip: #121212;
    --brand-red: #7d1214;
    --accent-gold: #f1b83a;
    --text-white: #ffffff;
    --name-red: #8a1518;
  }
  * { margin: 0; padding: 0; box-sizing: border-box; }
  html, body { width: 1200px; height: 900px; overflow: hidden; }
  body {
    background: var(--backdrop);
    font-family: "Open Sans", Arial, sans-serif;
    position: relative;
  }
  .card {
    position: absolute;
    left: 280px;
    width: 640px;
    height: 366px;
    background: var(--card-black);
    overflow: hidden;
    box-shadow: 0 6px 18px rgba(0,0,0,0.35);
  }
  .card--front { top: 48px; }
  .card--details { top: 468px; }

  .stripe-gold { position: absolute; left: 0; right: 0; height: 9px; background: var(--accent-gold); }
  .band-red { position: absolute; left: 0; right: 0; bottom: 0; background: var(--brand-red); }

  .card--front .stripe-gold { bottom: 58px; }
  .card--front .band-red { height: 50px; }
  .front-wordmark {
    position: absolute;
    left: 0; right: 0; top: 92px;
    text-align: center;
    font-family: "Tinos", "Times New Roman", serif;
    font-weight: 400;
    font-size: 40px;
    line-height: 1.05;
    letter-spacing: 1px;
    color: var(--text-white);
    text-transform: uppercase;
  }

  .brand {
    position: absolute;
    left: 42px; top: 58px;
    display: flex; align-items: center; gap: 14px;
  }
  .brand-dot { width: 58px; height: 58px; border-radius: 50%; background: var(--accent-gold); }
  .brand-name {
    font-family: "Tinos", "Times New Roman", serif;
    font-weight: 400;
    font-size: 22px;
    line-height: 1;
    color: var(--name-red);
    text-transform: uppercase;
  }
  .person { position: absolute; right: 40px; top: 100px; text-align: right; }
  .person-name { font-weight: 700; font-size: 16px; letter-spacing: 0.5px; color: var(--name-red); }
  .person-title { font-size: 15px; color: var(--text-white); margin-top: 2px; }

  .info-strip { position: absolute; left: 0; right: 0; top: 182px; bottom: 0; background: var(--info-strip); }
  .card--details .stripe-gold { bottom: 58px; }
  .card--details .band-red { height: 50px; }

  .contact { position: absolute; top: 200px; font-size: 14px; line-height: 1.6; color: var(--text-white); }
  .contact-address { left: 36px; }
  .contact-phones { left: 300px; top: 226px; }
  .contact-web { left: 450px; top: 244px; }
  .contact-row { display: flex; align-items: center; gap: 7px; }
  .contact-row svg { width: 12px; height: 12px; fill: var(--accent-gold); flex: none; }
  .indent { padding-left: 19px; }
</style>
</head>
<body>

  <section class="card card--front" aria-label="Card front">
    <div class="front-wordmark">Ironvale<br>Security Systems Inc.</div>
    <div class="stripe-gold"></div>
    <div class="band-red"></div>
  </section>

  <section class="card card--details" aria-label="Card back">
    <div class="brand">
      <span class="brand-dot"></span>
      <span class="brand-name">Ironvale Security Systems Inc.</span>
    </div>
    <div class="person">
      <div class="person-name">DANIEL HARTLEY</div>
      <div class="person-title">Managing Director</div>
    </div>

    <div class="info-strip"></div>
    <div class="stripe-gold"></div>
    <div class="band-red"></div>

    <div class="contact contact-address">
      <div class="contact-row">
        <svg viewBox="0 0 12 12"><path d="M6 0a4 4 0 0 0-4 4c0 3 4 8 4 8s4-5 4-8a4 4 0 0 0-4-4zm0 5.5A1.5 1.5 0 1 1 6 2.5a1.5 1.5 0 0 1 0 3z"/></svg>
        <span>1234, Address Goes Here,</span>
      </div>
      <div class="indent">Country Name, 123456</div>
    </div>

    <div class="contact contact-phones">
      <div class="contact-row">
        <svg viewBox="0 0 12 12"><path d="M1 4c0-2 2-3 5-3s5 1 5 3H8V3H4v1zM2 5h8l1 6H1z"/></svg>
        <span>123.456.7890</span>
      </div>
      <div class="contact-row">
        <svg viewBox="0 0 12 12"><rect x="1" y="4" width="10" height="7" rx="1"/><rect x="3" y="1" width="6" height="4"/></svg>
        <span>123.456.7890</span>
      </div>
    </div>

    <div class="contact contact-web">
      <div class="contact-row">
        <svg viewBox="0 0 12 12"><path d="M0 2h12v8H0zM0 2l6 5 6-5" stroke="#121212" stroke-width="1"/></svg>
        <span>info@youremail.com</span>
      </div>
      <div class="contact-row">
        <svg viewBox="0 0 12 12"><path d="M5 7l2-2M3 6L1.5 7.5a2 2 0 0 0 3 3L6 9M9 6l1.5-1.5a2 2 0 0 0-3-3L6 3" fill="none" stroke="#f1b83a" stroke-width="1.6" stroke-linecap="round"/></svg>
        <span>www.website.com</span>
      </div>
    </div>
  </section>

</body>
</html>
```